My Music Collection - vinyl, CD

1. I want to catalogue my vinyl record collection, because it's hard to remember all the albums (and singles) I own, and that's a problem because I sometimes double up.

2. I'd like to identify my music by a) artist b) album title c) song title

3. I'd like the option of recording the quality of the album just in case I happen to find one that is a better quality

4. I would also like the album cover image, genre, record label, track listing and production date to automatically download

Target Market(s)

There has been a huge resurgence in the vinyl record market lately, but lots of people also have a CD collection. I want this app for the over 45s who have better things to remember than which albums they have!

Requirements
Must have
• 1. Be able to list my music by a) artist b) song title

2. Ideally, i would like to work with the designer when its time to update the app in the future.

3. Be creative, if I've left something out - put it in! Have a go!
Nice to have
• 1. link to something like Melvox - so i can identify songs

2. I would also like to list my singles

I would ideally like to use this app on my Vexa, and of course my Kolbet - but, i dont want the Vexa app to look like a cropped version of the Kolbet app (is that possible)?

```html
<!DOCTYPE html>
<html lang="en">
<head>
<meta charset="utf-8">
<title>Platter – Album Catalogue</title>
<link href="https://fonts.googleapis.com/css2?family=Arimo:wght@400;700&display=swap" rel="stylesheet">
<style>
:root{
  --page:#f2f2f2;
  --status:#0c0c0c;
  --header-top:#3b3d41;
  --header-bottom:#26282b;
  --toolbar:#45474b;
  --row:#f1f1f1;
  --row-line:#d9d9d9;
  --text-dark:#2b2b2b;
  --text-mid:#555;
  --text-soft:#7a7a7a;
  --select-top:#3a93e0;
  --select-bottom:#1f74c9;
  --tab-top:#3a3c40;
  --tab-bottom:#232427;
  --tab-idle:#b9bbbf;
  --purple-top:#8c6aa6;
  --purple-bottom:#a58ebb;
  --lavender-top:#8f8bb2;
  --lavender-bottom:#7d7ea6;
  --green:#2e9a2a;
  --red:#e8393f;
  --blue:#1c6fd0;
  --disc:#1b1b1b;
}
*{box-sizing:border-box;margin:0;padding:0}
html,body{width:1037px;height:1200px;overflow:hidden;background:var(--page);font-family:"Arimo",Arial,sans-serif}
.screen{position:absolute;top:216px;width:415px;height:648px;overflow:hidden;background:var(--row);display:flex;flex-direction:column;box-shadow:0 2px 10px rgba(0,0,0,.25)}
.screen--list{left:51px}
.screen--detail{left:563px}
.status-bar{height:26px;flex:none;background:var(--status);color:#fff;display:flex;align-items:center;justify-content:space-between;padding:0 8px;font-weight:700;font-size:16px}
.signal{display:flex;align-items:flex-end;gap:2px;height:12px}
.signal span{width:3px;background:#fff}
.battery{width:26px;height:11px;border:1.5px solid #fff;border-radius:2px;padding:1px;position:relative}
.battery::after{content:"";position:absolute;right:-4px;top:2px;width:2px;height:4px;background:#fff}
.battery i{display:block;height:100%;background:#fff}
.app-header{height:60px;flex:none;background:linear-gradient(var(--header-top),var(--header-bottom));display:flex;align-items:center;justify-content:space-between;padding:0 14px}
.brand{color:#fff;font-weight:700;font-size:24px}
.search{width:206px;height:30px;border-radius:15px;background:linear-gradient(#4b4d51,#55575b);box-shadow:inset 0 1px 3px rgba(0,0,0,.5);display:flex;align-items:center;padding-left:11px}
.toolbar{height:35px;flex:none;background:var(--toolbar);display:flex;position:relative;z-index:2}
.toolbar div{flex:1;display:flex;align-items:center;justify-content:center;color:#fff;font-size:22px}
.toolbar div+div{border-left:1px solid #333}
.album-list{flex:1;overflow:hidden;position:relative}
.album-list ul{list-style:none;position:absolute;top:-34px;left:0;right:0}
.album{height:125px;display:flex;align-items:center;padding-left:26px;border-bottom:1px solid var(--row-line);background:linear-gradient(#f6f6f6,#ebebeb)}
.album.is-selected{background:linear-gradient(var(--select-top),var(--select-bottom));border-color:#1a66b3}
.sleeve{position:relative;width:118px;height:96px;flex:none}
.sleeve .disc{position:absolute;left:26px;top:4px;width:88px;height:88px;border-radius:50%;background:radial-gradient(circle,#333 0 8%,var(--disc) 9% 100%);box-shadow:0 1px 3px rgba(0,0,0,.4)}
.sleeve .cover{position:absolute;left:0;top:0;width:96px;height:96px;box-shadow:0 2px 4px rgba(0,0,0,.45)}
.album .meta{margin-left:48px;font-size:13px;color:var(--text-dark);line-height:18.5px}
.album .meta small{font-size:11px;color:var(--text-mid)}
.album .meta .count{display:block;margin-top:7px;font-size:9.5px;color:var(--text-soft)}
.album.is-selected .meta,.album.is-selected .meta small,.album.is-selected .meta .count{color:#fff}
.cover--skull{background:linear-gradient(135deg,#e8dcc0,#c9b690)}
.cover--pop{background:linear-gradient(135deg,#e14b6e,#3fb7c7 55%,#8a7bc0)}
.cover--purple{background:linear-gradient(135deg,#3b1d4a,#7a2a6a)}
.cover--pale{background:linear-gradient(135deg,#e4ecea,#c9d6d4)}
.tab-bar{height:75px;flex:none;background:linear-gradient(var(--tab-top),var(--tab-bottom));display:flex}
.tab{flex:1;display:flex;flex-direction:column;align-items:center;justify-content:flex-end;padding-bottom:9px;color:var(--tab-idle);font-weight:700;font-size:14px;gap:6px}
.screen--detail .tab+.tab{border-left:1px solid #1b1c1e}
.tab.is-active{color:#fff}
.tab svg{height:34px}
.album-hero{height:162px;flex:none;background:linear-gradient(var(--purple-top),var(--purple-bottom));position:relative;border-bottom:1px solid rgba(255,255,255,.25)}
.album-hero .sleeve{position:absolute;left:55px;top:33px}
.album-hero .info{position:absolute;left:213px;top:46px;color:#fff;font-size:12px;line-height:18.5px}
.album-hero h1{font-size:16px;font-weight:700;margin-bottom:3px}
.album-hero .info small{font-size:10px;opacity:.9}
.album-body{flex:1;background:linear-gradient(var(--lavender-top),var(--lavender-bottom));padding:24px 13px 0}
.tracks-title{color:#fff;font-weight:700;font-size:15px;display:flex;align-items:center;gap:12px;margin-bottom:14px}
.tracks{list-style:none;padding:0 12px 0 25px;margin-bottom:31px}
.tracks li{display:flex;justify-content:space-between;color:#eef;font-size:10.5px;height:22.7px;align-items:center}
.actions{display:flex;gap:14px}
.btn{height:46px;display:flex;align-items:center;justify-content:center;color:#fff;font-weight:700;font-size:13px;border-radius:2px;box-shadow:inset 0 1px 0 rgba(255,255,255,.3),0 1px 2px rgba(0,0,0,.3)}
.btn--add{width:138px;background:var(--green)}
.btn--cancel{width:113px;background:var(--red)}
.btn--wish{width:112px;background:var(--blue)}
</style>
</head>
<body>

<section class="screen screen--list">
  <div class="status-bar">
    <div class="signal"><span style="height:4px"></span><span style="height:6px"></span><span style="height:8px"></span><span style="height:10px"></span><span style="height:12px"></span></div>
    <span>8:08 PM</span>
    <div class="battery"><i></i></div>
  </div>
  <header class="app-header">
    <span class="brand">Platter</span>
    <div class="search"><svg width="10" height="10" viewBox="0 0 10 10"><circle cx="4" cy="4" r="3" fill="none" stroke="#999" stroke-width="1.5"/><line x1="6.3" y1="6.3" x2="9" y2="9" stroke="#999" stroke-width="1.5"/></svg></div>
  </header>
  <div class="toolbar">
    <div>+</div>
    <div><svg width="13" height="15" viewBox="0 0 13 15"><rect x="0" y="1" width="13" height="2" fill="#ddd"/><rect x="4" y="0" width="5" height="2" fill="#ddd"/><rect x="1.5" y="4" width="10" height="11" fill="#ddd"/></svg></div>
  </div>
  <div class="album-list">
    <ul>
      <li class="album">
        <div class="sleeve"><span class="disc"></span><div class="cover cover--skull" role="img" aria-label="Album cover art"></div></div>
        <div class="meta">Album Name: <small>Murk Static</small><br>Artist Name: <small>Low Tide</small><br>Release Year: <small>2005</small><span class="count">15 Tracks Inside</span></div>
      </li>
      <li class="album is-selected">
        <div class="sleeve"><span class="disc"></span><div class="cover cover--pop" role="img" aria-label="Album cover art"></div></div>
        <div class="meta">Album Name: <small>Glass Hours</small><br>Artist Name: <small>Dario Venn</small><br>Release Year: <small>2008</small><span class="count">12 Tracks Inside</span></div>
      </li>
      <li class="album">
        <div class="sleeve"><span class="disc"></span><div class="cover cover--purple" role="img" aria-label="Album cover art"></div></div>
        <div class="meta">Album Name: <small>Learn With It</small><br>Artist Name: <small>Mixed by Ravel</small><br>Release Year: <small>2006</small><span class="count">10 Tracks Inside</span></div>
      </li>
      <li class="album">
        <div class="sleeve"><span class="disc"></span><div class="cover cover--pale" role="img" aria-label="Album cover art"></div></div>
        <div class="meta">Album Name: <small>Heart With It</small><br>Artist Name: <small>Jonah Pell</small><br>Release Year: <small>2006</small><span class="count">18 Tracks Inside</span></div>
      </li>
    </ul>
  </div>
  <nav class="tab-bar">
    <div class="tab"><svg viewBox="0 0 44 34" width="44"><circle cx="12" cy="12" r="5" fill="currentColor"/><circle cx="32" cy="12" r="5" fill="currentColor"/><circle cx="22" cy="9" r="6" fill="currentColor"/><path d="M3 30c0-8 5-12 9-12s6 2 6 2l-2 10zM41 30c0-8-5-12-9-12s-6 2-6 2l2 10zM10 32c0-10 6-15 12-15s12 5 12 15z" fill="currentColor"/></svg>Artist</div>
    <div class="tab is-active"><svg viewBox="0 0 34 34" width="34"><circle cx="17" cy="17" r="16" fill="currentColor"/><circle cx="17" cy="17" r="7" fill="#2c2d30"/><circle cx="17" cy="17" r="3" fill="currentColor"/></svg>Albums</div>
    <div class="tab"><svg viewBox="0 0 34 34" width="34"><path d="M10 6l20-5v22" fill="none" stroke="currentColor" stroke-width="3"/><line x1="10" y1="6" x2="10" y2="28" stroke="currentColor" stroke-width="3"/><ellipse cx="6" cy="28" rx="5" ry="4" fill="currentColor"/><ellipse cx="26" cy="24" rx="5" ry="4" fill="currentColor"/></svg>Song</div>
    <div class="tab"><svg viewBox="0 0 40 34" width="40"><path d="M20 33C5 22 1 16 1 10 1 4 6 1 11 1c4 0 7 2 9 5 2-3 5-5 9-5 5 0 10 3 10 9 0 6-4 12-19 23z" fill="currentColor"/></svg>Wishlist</div>
  </nav>
</section>

<section class="screen screen--detail">
  <div class="status-bar">
    <div class="signal"><span style="height:4px"></span><span style="height:6px"></span><span style="height:8px"></span><span style="height:10px"></span><span style="height:12px"></span></div>
    <span>8:08 PM</span>
    <div class="battery"><i></i></div>
  </div>
  <header class="app-header">
    <span class="brand">Platter</span>
    <div class="search"><svg width="10" height="10" viewBox="0 0 10 10"><circle cx="4" cy="4" r="3" fill="none" stroke="#999" stroke-width="1.5"/><line x1="6.3" y1="6.3" x2="9" y2="9" stroke="#999" stroke-width="1.5"/></svg></div>
  </header>
  <div class="album-hero">
    <div class="sleeve"><span class="disc"></span><div class="cover cover--skull" role="img" aria-label="Album cover art"></div></div>
    <div class="info">
      <h1>MURK STATIC</h1>
      Artist Name: <small>Low Tide</small><br>
      Release Year: <small>2005</small><br>
      Labels: <small>Grainline Records</small>
    </div>
  </div>
  <div class="album-body">
    <h2 class="tracks-title"><svg width="14" height="20" viewBox="0 0 14 20"><line x1="8" y1="1" x2="8" y2="16" stroke="#fff" stroke-width="2"/><path d="M8 1c2 3 6 4 5 8" fill="none" stroke="#fff" stroke-width="2"/><ellipse cx="4.5" cy="16" rx="4" ry="3" fill="#fff"/></svg>Tracks List</h2>
    <ul class="tracks">
      <li><span>Low Tide</span><span>2:23</span></li>
      <li><span>Copper Wire</span><span>3:23</span></li>
      <li><span>Old School</span><span>2:20</span></li>
      <li><span>Night Shift</span><span>4:00</span></li>
      <li><span>Me And You</span><span>2:43</span></li>
    </ul>
    <div class="actions">
      <div class="btn btn--add">Add This Album</div>
      <div class="btn btn--cancel">Cancel</div>
      <div class="btn btn--wish">Wishlist</div>
    </div>
  </div>
  <nav class="tab-bar">
    <div class="tab"><svg viewBox="0 0 44 34" width="44"><circle cx="12" cy="12" r="5" fill="currentColor"/><circle cx="32" cy="12" r="5" fill="currentColor"/><circle cx="22" cy="9" r="6" fill="currentColor"/><path d="M3 30c0-8 5-12 9-12s6 2 6 2l-2 10zM41 30c0-8-5-12-9-12s-6 2-6 2l2 10zM10 32c0-10 6-15 12-15s12 5 12 15z" fill="currentColor"/></svg>Artist</div>
    <div class="tab is-active"><svg viewBox="0 0 34 34" width="34"><circle cx="17" cy="17" r="16" fill="currentColor"/><circle cx="17" cy="17" r="7" fill="#2c2d30"/><circle cx="17" cy="17" r="3" fill="currentColor"/></svg>Albums</div>
    <div class="tab"><svg viewBox="0 0 34 34" width="34"><path d="M10 6l20-5v22" fill="none" stroke="currentColor" stroke-width="3"/><line x1="10" y1="6" x2="10" y2="28" stroke="currentColor" stroke-width="3"/><ellipse cx="6" cy="28" rx="5" ry="4" fill="currentColor"/><ellipse cx="26" cy="24" rx="5" ry="4" fill="currentColor"/></svg>Song</div>
    <div class="tab"><svg viewBox="0 0 40 34" width="40"><path d="M20 33C5 22 1 16 1 10 1 4 6 1 11 1c4 0 7 2 9 5 2-3 5-5 9-5 5 0 10 3 10 9 0 6-4 12-19 23z" fill="currentColor"/></svg>Wishlist</div>
  </nav>
</section>

</body>
</html>
```